Probate (Legal) Wordpress Design with Coding for Online Company

I need a Wordpress design with coding, pictures, content to be provided by me, fully responsive, and development. This is for a 6-7 page design.

Pages Needed: Home/About/Probate/Process/FAQ/Contact Us/Blog.

The home page should be organized as followed:
-Steps in Probate: Gather; Implement; Close (each step will come with content)
-Flat-Fee Price & Savings: Content will go here with a button to contact us (phone number) or just the phone number.
-You Have Questions, We Have Answers: five questions with content. Only one question answer to show at a time when clicked on the question from the list.
-Get to Know Us: a brief description with content about what we do and who we are.

Main image slogan: Helping Californians deal with loss with DIGNITY & UNDERSTATING (you may use a better slogan if you wish).

The Contact page should not have a map since we are an online company. We service the entire state of California in every county and city.

The About page should be simple, direct, and easy on the eye. It should have a brief description of who we are and it should have no more than 6 reasons why the client should hire us.

About our online California company. We are not attorneys but legal document assistants who prepare legal documents for probate estate when someone dies with or without a will and assets need to be distributed. We have a flat-fee for Formal Probate of $999 and $699 for Informal Probate. We are an online company and offer our services to the entire state of California in every county. We do everything over the phone and email. The turn around time for us to prepare the initial legal paperwork for the client is within 3-5 business days. We can prepare, file, serve and manage a probate matter from petition to closing. We are not attorneys so our prices are very affordable compare to the attorney.

The company name for the website will be www.velmarhollow.com, The Velmar Hollow Group.

I do not have a logo yet. The colors of the website should be easy on the eye and calming. THE SITE SHOULD BE SIMPLE AND STRAIGHT TO THE POINT. EASY TO NAVIGATE.

The company phone number should be very visible and should stand out to the client. It should also be clickable and ready to dial for smartphone users.

I do not want a contact form on the homepage. THE MAIN THING IS FOR THE POTENTIAL CLIENT TO CALL OUR OFFICE TO SIGN UP.

I do like some images of family or people since we are dealing with people who just lost a loved one. Not all the images have to be of people.

The site should not look like we practice law or that people can mistake us for attorneys.

Target Market(s)

People who just lost a loved one who had property, assets, in California but died with or without a will or trust. This is for people looking to hire non-attorneys.

Coding

Coded - Design and coding required

Font styles to use
Serif

Colors

Designer to choose colors to be used in the design.

Requirements
Must have
• Refer to Project Description.
Nice to have
• The sample images provided is what I am attracted to for the homepage image.
Should not have

```html
<!DOCTYPE html>
<html lang="en">
<head>
<meta charset="utf-8">
<title>The Velmar Hollow Group — Probate Document Assistance</title>
<link rel="stylesheet" href="https://fonts.googleapis.com/css2?family=Lato:wght@400;700;900&display=swap">
<style>
:root{
  --accent:#fc4a0f;
  --ink:#333333;
  --body:#444444;
  --topbar:#4b4b4b;
  --panel:#f2f2f2;
  --white:#ffffff;
  --line:#d9d9d9;
  --icon:#6b6b6b;
}
*{box-sizing:border-box;margin:0;padding:0}
html,body{width:1200px;height:2466px;overflow:hidden}
body{font-family:"Lato",Arial,sans-serif;color:var(--ink);background:var(--white);position:relative}
a{color:inherit;text-decoration:none}
.abs{position:absolute}

/* top bar */
.topbar{left:0;top:0;width:1200px;height:58px;background:var(--topbar)}
.social{display:flex;gap:14px;align-items:center}
.social span{width:22px;height:22px;border-radius:50%;background:#d8d8d8;display:block}
.topbar .social{position:absolute;left:76px;top:18px}
.phone{position:absolute;right:74px;top:14px;color:var(--white);font-weight:700;font-size:23px;display:flex;align-items:center;gap:14px}

/* header */
.header{left:0;top:58px;width:1200px;height:78px;background:var(--white)}
.brand{position:absolute;left:76px;top:24px;font-size:28px;font-weight:700;color:var(--ink);letter-spacing:.3px}
.nav{position:absolute;right:74px;top:30px;display:flex;gap:0}
.nav a{font-size:13px;font-weight:700;text-transform:uppercase;padding:0 19px 12px;position:relative;color:var(--ink)}
.nav a.active{color:var(--accent)}
.nav a.active::after{content:"";position:absolute;left:0;right:0;bottom:0;height:2px;background:var(--accent)}

/* hero */
.hero{left:0;top:136px;width:1200px;height:525px;background:linear-gradient(100deg,#8c8a5e 0%,#b7a27f 30%,#d8c7ad 55%,#c9b59d 75%,#9a8a73 100%)}
.hero-copy{position:absolute;left:0;right:0;top:214px;text-align:center;color:var(--white);text-shadow:0 1px 6px rgba(0,0,0,.35)}
.hero-copy .kicker{font-size:31px;font-weight:700;display:block}
.hero-copy .headline{font-size:56px;font-weight:900;display:block;margin-top:2px;letter-spacing:.5px}
.dots{position:absolute;top:484px;left:570px;display:flex;gap:6px}
.dots span{width:9px;height:9px;border-radius:50%;background:var(--white)}
.dots span.on{background:var(--accent)}

/* buttons */
.btn{display:flex;align-items:center;justify-content:center;background:var(--accent);color:var(--white);font-weight:700;font-size:17px;text-transform:uppercase;border-radius:25px;height:49px}

/* who we are */
.section-title{font-size:28px;font-weight:700;text-transform:uppercase;color:var(--ink)}
.who{left:0;top:725px;width:1200px;text-align:center}
.who p{margin:28px auto 0;width:1050px;font-size:16.5px;line-height:30.5px;color:var(--body)}
.who .btn{width:208px;margin:30px auto 0}

/* what we do */
.what{left:0;top:1031px;width:1200px;height:384px;background:var(--panel)}
.what-photo{position:absolute;left:0;top:0;width:588px;height:384px;background:linear-gradient(120deg,#f3ddc9 0%,#caa58a 35%,#59616b 70%,#2f3a4a 100%)}
.what-copy{position:absolute;left:626px;top:46px;width:500px}
.what-copy p{margin-top:18px;font-size:16.5px;line-height:30.5px;color:var(--body)}
.what-copy .btn{width:208px;margin-top:26px;margin-left:-1px}

/* steps */
.steps{left:0;top:1473px;width:1200px;text-align:center}
.step{position:absolute;width:320px;top:70px;text-align:center}
.step svg{display:block;margin:0 auto}
.step h3{margin-top:16px;font-size:18.5px;font-weight:700;color:var(--accent);text-transform:uppercase}
.step p{margin-top:12px;font-size:16px;line-height:23px;color:var(--body)}
.step-arrow{position:absolute;top:76px}

/* pricing + faq */
.band{left:0;top:1802px;width:1200px;height:493px;background:var(--panel)}
.price-card{position:absolute;left:76px;top:51px;width:512px;height:391px;background:linear-gradient(160deg,#4a4340 0%,#2c2a2a 55%,#3b3532 100%);color:var(--white);text-align:center}
.price-card h2{margin-top:41px;font-size:36px;line-height:38px;font-weight:700;text-transform:uppercase}
.price-card p{margin:22px auto 0;width:450px;font-size:16px;line-height:26px}
.price-card .btn{width:208px;margin:26px auto 0}

.faq{position:absolute;left:613px;top:48px;width:513px}
.faq h2{font-size:28px;font-weight:700;text-transform:uppercase}
.faq-item{background:var(--white);border:1px solid var(--line);margin-top:11px;padding:0 16px}
.faq-list{margin-top:10px}
.faq-list .faq-item:first-child{margin-top:0}
.faq-q{display:flex;justify-content:space-between;align-items:center;height:43px;font-size:16px;font-weight:700;color:var(--ink)}
.faq-item.open .faq-q{height:38px}
.faq-a{font-size:13px;line-height:19.5px;color:var(--body);padding-bottom:14px;width:470px}

/* footer */
.footer{left:0;top:2295px;width:1200px;height:171px;background:var(--white)}
.foot-nav{position:absolute;left:76px;top:36px;display:flex;gap:29px}
.foot-nav a{font-size:13px;text-transform:uppercase;color:var(--ink)}
.copyright{position:absolute;left:76px;top:75px;font-size:12px;color:var(--body)}
.footer .social{position:absolute;left:76px;top:110px}
.footer .social span{background:#6e6e6e}
.subscribe{position:absolute;left:794px;top:34px;width:332px}
.subscribe h4{font-size:14px;font-weight:700;text-transform:uppercase}
.subscribe-row{display:flex;gap:14px;margin-top:20px}
.subscribe-row .field{width:242px;height:40px;border:1px solid #c8c8c8;font-size:12px;color:#777;padding:12px 10px}
.subscribe-row .go{width:76px;height:40px;background:var(--accent);color:var(--white);font-size:11px;font-weight:700;display:flex;align-items:center;justify-content:center;text-transform:uppercase}
</style>
</head>
<body>

<div class="abs topbar">
  <div class="social"><span></span><span></span><span></span><span></span><span></span></div>
  <a class="phone" href="tel:18005550148">
    <svg width="18" height="18" viewBox="0 0 24 24"><path fill="#ffffff" d="M6.6 10.8a15.1 15.1 0 0 0 6.6 6.6l2.2-2.2c.3-.3.7-.4 1-.2 1.1.4 2.3.6 3.6.6.6 0 1 .4 1 1V20c0 .6-.4 1-1 1A17 17 0 0 1 3 4c0-.6.4-1 1-1h3.5c.6 0 1 .4 1 1 0 1.3.2 2.5.6 3.6.1.3 0 .7-.2 1z"/></svg>
    1-800-555-0148
  </a>
</div>

<header class="abs header">
  <div class="brand">THE VELMAR HOLLOW</div>
  <nav class="nav">
    <a class="active" href="#">Home</a><a href="#">About</a><a href="#">Probate</a><a href="#">Process</a><a href="#">FAQ</a><a href="#">Contact Us</a><a href="#">Blog</a>
  </nav>
</header>

<section class="abs hero" role="img" aria-label="Photo of a smiling multi-generation family gathered outdoors">
  <div class="hero-copy">
    <span class="kicker">Helping Californians Deal with Loss with</span>
    <span class="headline">DIGNITY &amp; UNDERSTATING</span>
  </div>
  <div class="dots"><span class="on"></span><span></span><span></span><span></span></div>
</section>

<section class="abs who">
  <h2 class="section-title">Who We Are</h2>
  <p>About our online California company. We are not attorneys but legal document assistants who prepare legal documents for probate estate when someone dies with or without a will and assets need to be distributed. We have a flat-fee for Formal Probate of $999 and $699 for Informal Probate. We are an online company and offer our services to the entire state of California in every county.</p>
  <a class="btn" href="#">Read More</a>
</section>

<section class="abs what">
  <div class="what-photo" role="img" aria-label="Photo of a person signing documents at a desk with coffee, notebook and tablet"></div>
  <div class="what-copy">
    <h2 class="section-title">What We Do</h2>
    <p>Aliquam molestie, mi et imperdiet euismod, dui purus auctor tellus,&nbsp; et interdum lacus lectus et ante. Sed accumsan sollicitudin sapien, sit amet adipiscing turpis gravida ac. In congue, neque ac lobortis volutpat, libero mauris varius mi, vitae suscipit ipsum ligula vitae risus.</p>
    <a class="btn" href="#">Read More</a>
  </div>
</section>

<section class="abs steps">
  <h2 class="section-title">Steps in Probate</h2>

  <div class="step" style="left:80px">
    <svg width="66" height="62" viewBox="0 0 66 62" fill="var(--icon)">
      <circle cx="33" cy="16" r="10"/><circle cx="13" cy="21" r="7"/><circle cx="53" cy="21" r="7"/>
      <path d="M18 60v-14a15 15 0 0 1 30 0v14z"/>
      <path d="M2 56v-12a11 11 0 0 1 18-8 19 19 0 0 0-4 11v9z"/>
      <path d="M64 56v-12a11 11 0 0 0-18-8 19 19 0 0 1 4 11v9z"/>
    </svg>
    <h3>1. Gather</h3>
    <p>Vestibulum ante ipsum primis in faucibus orci luctus et ultrices posuere cubilia egestas risus in magna..</p>
  </div>

  <svg class="step-arrow" style="left:385px" width="68" height="50" viewBox="0 0 68 50" fill="none" stroke="#8a8a8a" stroke-width="2">
    <path d="M2 4 C 14 30, 36 44, 64 40"/><path d="M54 32 L64 40 L53 46"/>
  </svg>

  <div class="step" style="left:440px">
    <svg width="60" height="60" viewBox="0 0 60 60" fill="none" stroke="var(--icon)" stroke-width="8">
      <path d="M10 26 A21 21 0 0 1 47 16"/><path d="M50 34 A21 21 0 0 1 13 44"/>
      <path d="M52 4 V22 H34" stroke-width="0" fill="var(--icon)"/>
      <polygon points="54,4 54,24 34,24" fill="var(--icon)" stroke="none"/>
      <polygon points="6,56 6,36 26,36" fill="var(--icon)" stroke="none"/>
    </svg>
    <h3>2. Implement</h3>
    <p>Vestibulum ante ipsum primis in faucibus orci luctus et ultrices posuere cubilia egestas risus in magna..</p>
  </div>

  <svg class="step-arrow" style="left:745px" width="68" height="50" viewBox="0 0 68 50" fill="none" stroke="#8a8a8a" stroke-width="2">
    <path d="M2 46 C 10 22, 32 8, 62 8"/><path d="M52 2 L62 8 L53 16"/>
  </svg>

  <div class="step" style="left:798px">
    <svg width="50" height="60" viewBox="0 0 50 60">
      <path d="M8 12 L42 46 M42 12 L8 46" stroke="var(--icon)" stroke-width="11" stroke-linecap="round"/>
    </svg>
    <h3>3. Close</h3>
    <p>Vestibulum ante ipsum primis in faucibus orci luctus et ultrices posuere cubilia egestas risus in magna..</p>
  </div>
</section>

<section class="abs band">
  <div class="price-card" role="img" aria-label="Dark photo of coins and a calculator behind the pricing message">
    <h2>Flat-Fee Price<br>&amp; Savings</h2>
    <p>Aliquam molestie, mi et imperdiet euismod, dui purus auctor tellus, et interdum lacus lectus et ante. Sed accumsan sollicitudin sapien, sit amet adipiscing turpis gravida ac. In congue, neque ac lobortis volutpat, libero mauris varius mi, vitae suscipit ipsum&nbsp; ligula vitae risus..</p>
    <a class="btn" href="tel:18005550148">Contact Us</a>
  </div>

  <div class="faq">
    <h2>FAQ</h2>
    <div class="faq-list">
      <div class="faq-item open">
        <div class="faq-q">Lorem ipsum dolor sit amet, consectetur adipiscing?
          <svg width="14" height="14" viewBox="0 0 14 14"><circle cx="7" cy="7" r="7" fill="var(--accent)"/><rect x="3" y="6" width="8" height="2" fill="#fff"/></svg>
        </div>
        <div class="faq-a">Vestibulum vel metus sit amet turpis bibendum tincidunt vel sit amet quam. Pellentesque habitant morbi tristique senectus. Duis aliquam nibh a dui iaculis viverra id a velit.</div>
      </div>
      <div class="faq-item"><div class="faq-q">Lorem ipsum dolor sit amet, consectetur adipiscing?
        <svg width="14" height="14" viewBox="0 0 14 14"><circle cx="7" cy="7" r="7" fill="#555"/><rect x="3" y="6" width="8" height="2" fill="#fff"/><rect x="6" y="3" width="2" height="8" fill="#fff"/></svg></div></div>
      <div class="faq-item"><div class="faq-q">Lorem ipsum dolor sit amet, consectetur adipiscing?
        <svg width="14" height="14" viewBox="0 0 14 14"><circle cx="7" cy="7" r="7" fill="#555"/><rect x="3" y="6" width="8" height="2" fill="#fff"/><rect x="6" y="3" width="2" height="8" fill="#fff"/></svg></div></div>
      <div class="faq-item"><div class="faq-q">Lorem ipsum dolor sit amet, consectetur adipiscing?
        <svg width="14" height="14" viewBox="0 0 14 14"><circle cx="7" cy="7" r="7" fill="#555"/><rect x="3" y="6" width="8" height="2" fill="#fff"/><rect x="6" y="3" width="2" height="8" fill="#fff"/></svg></div></div>
      <div class="faq-item"><div class="faq-q">Lorem ipsum dolor sit amet, consectetur adipiscing?
        <svg width="14" height="14" viewBox="0 0 14 14"><circle cx="7" cy="7" r="7" fill="#555"/><rect x="3" y="6" width="8" height="2" fill="#fff"/><rect x="6" y="3" width="2" height="8" fill="#fff"/></svg></div></div>
    </div>
  </div>
</section>

<footer class="abs footer">
  <nav class="foot-nav">
    <a href="#">Home</a><a href="#">About</a><a href="#">Probate</a><a href="#">Process</a><a href="#">FAQ</a><a href="#">Contact Us</a><a href="#">Blog</a>
  </nav>
  <div class="copyright">Copyright © 2017. Company Name. All Right Reserved</div>
  <div class="social"><span></span><span></span><span></span><span></span><span></span></div>
  <div class="subscribe">
    <h4>Subscribe Email</h4>
    <div class="subscribe-row">
      <div class="field">Enter Email Address</div>
      <div class="go">Sign Up</div>
    </div>
  </div>
</footer>

</body>
</html>
```